Local business providing residential house cleaning services

We need a business card design that is "cute" or "cartoonish" while still maintaining a professional appeal. Tidal Sweepers is the name. We would like to use a "pin up girl" or maid next to the name with a broom or vacuum cleaner. We want the look to have a 50's American look to it. We are not sure if we want the pin up girl in a maid outfit or with a broom or vacuum cleaner but we hope some of you will be able to take these ideas and be creative. If you have any questions at all please don't hesitate to message me so that we can get the best design possible. Thank you very much and I look forward to seeing some designs! Mira Hollister

Target Market(s)

Upper class Americans that are busy and have money and want to come home to a clean house.

Industry/Entity Type

Cleaning Service

Contact Information for Business Card

Pin up girl incorporated into the card is a must.

Font styles to use
Decorative
Script

Requirements
Must have
• Pin up girl
Nice to have
• A crown used on the Q possibly.

```html
<!DOCTYPE html>
<html lang="en">
<head>
<meta charset="utf-8">
<title>Tidal Sweepers – Business Card</title>
<link rel="stylesheet" href="https://fonts.googleapis.com/css2?family=Righteous&display=swap">
<style>
  :root {
    --magenta: #e0127a;
    --blush: #fbe6f1;
    --paper: #fffafd;
    --charcoal: #2b2a29;
    --white: #ffffff;
    --stage: #efe9e4;
  }
  * { box-sizing: border-box; margin: 0; padding: 0; }
  html, body {
    width: 1076px;
    height: 1200px;
    overflow: hidden;
    background: var(--stage);
  }
  .business-card {
    position: absolute;
    left: 192px;
    top: 40px;
    width: 692px;
    height: 1120px;
    background: var(--magenta);
    font-family: "Righteous", sans-serif;
  }
  .card-face {
    position: absolute;
    inset: 30px;
    border: 9px dotted var(--magenta);
    background: radial-gradient(circle at 60% 45%, var(--paper) 0%, var(--paper) 35%, var(--blush) 100%);
  }
  .pinup-illustration {
    position: absolute;
    left: 220px;
    top: 40px;
    width: 365px;
    height: 450px;
    border-radius: 40px;
    background: linear-gradient(170deg, rgba(43,42,41,0.35) 0%, rgba(224,18,122,0.22) 55%, rgba(251,230,241,0) 100%);
  }
  .brand-name {
    position: absolute;
    left: 40px;
    top: 390px;
    color: var(--magenta);
    font-size: 78px;
    line-height: 0.95;
  }
  .brand-name .line-two { display: block; padding-left: 150px; font-size: 58px; }
  .contact-panel-bg {
    position: absolute;
    left: 55px;
    top: 600px;
    width: 520px;
    height: 420px;
    transform: rotate(-5deg);
  }
  .contact-panel-bg::before {
    content: "";
    position: absolute;
    inset: -12px;
    border: 6px dotted var(--magenta);
    border-radius: 30px;
  }
  .contact-panel-bg::after {
    content: "";
    position: absolute;
    inset: 0;
    background: var(--charcoal);
    border-radius: 24px;
  }
  .contact-details {
    position: absolute;
    left: 0;
    right: 0;
    top: 635px;
    text-align: center;
    color: var(--white);
  }
  .holder-name { font-size: 34px; }
  .contact-icon {
    display: block;
    margin: 22px auto 14px;
    width: 58px;
    height: 58px;
  }
  .contact-line { font-size: 28px; letter-spacing: 1px; }
  .contact-icon.mail { width: 64px; height: 44px; margin-top: 30px; }
</style>
</head>
<body>
  <div class="business-card">
    <div class="card-face"></div>

    <div class="pinup-illustration" role="img" aria-label="Illustration of a 1950s pin-up maid in a black dress and pink polka-dot apron, dusting with a pink feather duster"></div>

    <div class="brand-name">Tidal<span class="line-two">Sweepers</span></div>

    <div class="contact-panel-bg"></div>

    <div class="contact-details">
      <p class="holder-name">Mira Hollister</p>

      <svg class="contact-icon" viewBox="0 0 58 58" aria-hidden="true">
        <circle cx="29" cy="29" r="26" fill="none" stroke="var(--magenta)" stroke-width="4"/>
        <path d="M20 16c2-1 4 0 5 2l2 5c1 2 0 3-1 4l-2 2c2 4 5 7 9 9l2-2c1-1 2-2 4-1l5 2c2 1 3 3 2 5l-2 3c-2 2-6 2-11-1-6-4-11-9-14-15-3-5-2-9 1-13z" fill="var(--magenta)"/>
      </svg>
      <p class="contact-line">501-555-0148</p>

      <svg class="contact-icon mail" viewBox="0 0 64 44" aria-hidden="true">
        <rect x="3" y="3" width="58" height="38" rx="3" fill="none" stroke="var(--magenta)" stroke-width="4"/>
        <path d="M4 5l28 20 28-20M4 40l21-17M60 40L39 23" fill="none" stroke="var(--magenta)" stroke-width="4"/>
      </svg>
      <p class="contact-line">mira.hollister@example.com</p>
    </div>
  </div>
</body>
</html>
```